Alaska Law Firm Needs a Sticker Design

We need a design for stickers to put on already-printed brochures. We mail the brochures to potential clients so they can learn more about accident-induced injuries, insurance claims, legal representation, and our own law firm.

One of our lawyers wrote a book that provides a helpful overview of personal injury claims. We are offering this book for free to anyone who calls and requests it. Therefore, the sticker design should include one of the following phrases, or something very similar:
a) "Still have questions? Call and request our book-- for free!"
b) "Still have questions about auto accident claims? Call and request our book today."
c) "Still have questions about filing a claim? Call and request a free copy of our book."
d) "Still have questions? Call us today to request a free copy of our book, Clear Lanes Ahead."
e) "To learn more about automobile accidents and insurance, call today and request a free copy of our book."

The sticker should be approximately 3"x3" and may be a circle, square, rectangle, or ellipsis. The sticker will be placed on the back of the folder, which is light blue. We would like the sticker to match the color scheme of our website and the folder.

I will upload an image of the book cover as soon as I obtain it.

Law Firm

Font styles to use
Serif
Sans Serif

Requirements
Should not have
• Bright colors that aren't already used in the folder design. e.g. no bright orange, pink, chartreuse, turquoise, yellow, red.

```html
<!DOCTYPE html>
<html lang="en">
<head>
<meta charset="UTF-8">
<title>Free Book Sticker</title>
<link rel="stylesheet" href="https://fonts.googleapis.com/css2?family=Poppins:wght@600;700&display=swap">
<style>
  :root {
    --sticker-blue: #3d22fb;
    --ink-white: #ffffff;
    --accent-folder-blue: #a8d6ff;
    --page-bg: #ffffff;
  }
  html, body {
    margin: 0;
    padding: 0;
    width: 1200px;
    height: 1200px;
    overflow: hidden;
    background: var(--page-bg);
  }
  .sticker {
    position: relative;
    width: 1200px;
    height: 1200px;
    font-family: "Poppins", Arial, sans-serif;
  }
  .sticker-shape {
    position: absolute;
    inset: 0;
  }
  .message {
    position: absolute;
    left: 0;
    right: 0;
    top: 206px;
    margin: 0;
    text-align: center;
    font-weight: 600;
    font-size: 80px;
    line-height: 93px;
    letter-spacing: -0.5px;
    color: var(--ink-white);
  }
  .message .line { display: block; }
  .message .call-to-action { color: var(--accent-folder-blue); }
  .phone {
    position: absolute;
    left: 0;
    right: 0;
    top: 892px;
    display: flex;
    justify-content: center;
    align-items: center;
    gap: 26px;
    color: var(--ink-white);
    font-weight: 700;
    font-size: 92px;
    line-height: 96px;
    letter-spacing: 1px;
  }
  .phone-icon { width: 78px; height: 78px; flex: none; }
</style>
</head>
<body>
  <div class="sticker">
    <svg class="sticker-shape" width="1200" height="1200" viewBox="0 0 1200 1200" aria-hidden="true">
      <circle cx="600" cy="600" r="594" fill="var(--sticker-blue)"/>
      <circle cx="600" cy="600" r="567" fill="none" stroke="var(--ink-white)" stroke-width="11" stroke-dasharray="1.6 4.6"/>
    </svg>

    <p class="message">
      <span class="line">To learn more</span>
      <span class="line">about automobile</span>
      <span class="line">accidents</span>
      <span class="line">and insurance,</span>
      <span class="line call-to-action">Call today and</span>
      <span class="line call-to-action">request a free copy</span>
      <span class="line call-to-action">of our book.</span>
    </p>

    <div class="phone">
      <svg class="phone-icon" viewBox="0 0 74 74" aria-hidden="true">
        <circle cx="37" cy="37" r="33" fill="none" stroke="var(--ink-white)" stroke-width="4"/>
        <path d="M30 18 q-9 3 -8 14 q2 14 14 23 q8 5 13 1 l3 -3 l-8 -8 l-4 3 q-7 -4 -10 -12 l4 -3 z"
              fill="none" stroke="var(--ink-white)" stroke-width="3.5" stroke-linejoin="round"/>
      </svg>
      <span class="phone-number">907.555.0142</span>
    </div>
  </div>
</body>
</html>
```